Life Coaching Business - needs business card design with logo

I need a business card and logo design for a life coaching business I started based in Los Angeles. I offer services to clients that wish to bring more balance and overall wholeness to their lives. As of right now, the business name is "Marcus Ellery Coaching." An iidea I had for the logo was to be kind of a Yin-Yang symbol but with dolphins, as the dolphin has symbolic meaning for my business. Although I am really open to other ideas as long as it incorporates the idea of “balance,” “wholeness,” and “dolphins.”I also wanted to incorporate the color blue, maybe in the form of water, waves, or some sort of peaceful imagery.

```html
<!DOCTYPE html>
<html lang="en">
<head>
<meta charset="utf-8">
<title>Marcus Ellery Coaching – Business Cards</title>
<link rel="stylesheet" href="https://fonts.googleapis.com/css2?family=Open+Sans:wght@400;600&display=swap">
<style>
  :root {
    --page-bg: #6b6b6b;
    --card-dark: #141414;
    --card-mid: #2a2a2a;
    --ink-white: #f4f4f4;
    --ink-teal: #3ec9cc;
    --mark-blue: #3a8fd6;
  }
  * { margin: 0; padding: 0; box-sizing: border-box; }
  html, body {
    width: 1200px;
    height: 716px;
    overflow: hidden;
  }
  body {
    background: var(--page-bg);
    font-family: "Open Sans", sans-serif;
    display: flex;
    align-items: center;
    justify-content: center;
    gap: 60px;
  }
  .card {
    position: relative;
    width: 504px;
    height: 288px;
    border-radius: 6px;
    overflow: hidden;
    box-shadow: 0 10px 30px rgba(0,0,0,0.35);
  }
  .card-texture {
    position: absolute;
    inset: 0;
    background: radial-gradient(ellipse at 40% 35%, var(--card-mid) 0%, var(--card-dark) 75%);
  }
  .card-content {
    position: relative;
    height: 100%;
    display: flex;
    flex-direction: column;
    align-items: center;
    color: var(--ink-white);
    text-align: center;
  }
  .card--front .card-content { padding-top: 62px; }
  .card--back .card-content { padding-top: 38px; }
  .brand-mark {
    width: 96px;
    height: 96px;
    border-radius: 50%;
    background: var(--mark-blue);
    margin-bottom: 16px;
  }
  .business-name {
    font-size: 25px;
    font-weight: 400;
    letter-spacing: 0.2px;
    white-space: nowrap;
  }
  .details {
    display: flex;
    flex-direction: column;
    align-items: center;
  }
  .person-name {
    margin-top: 8px;
    font-size: 22px;
    color: var(--ink-teal);
  }
  .contact {
    margin-top: 4px;
    align-self: flex-start;
    text-align: left;
    padding-left: 8px;
  }
  .contact-line {
    font-size: 15px;
    line-height: 1.45;
    white-space: nowrap;
  }
  .contact-line--phone { padding-left: 40px; }
</style>
</head>
<body>

  <section class="card card--front" aria-label="Business card front">
    <div class="card-texture" role="img" aria-label="Water droplets on a dark surface"></div>
    <div class="card-content">
      <div class="brand-mark" aria-hidden="true"></div>
      <h1 class="business-name">Marcus Ellery Coaching.</h1>
    </div>
  </section>

  <section class="card card--back" aria-label="Business card with contact details">
    <div class="card-texture" role="img" aria-label="Water droplets on a dark surface"></div>
    <div class="card-content">
      <div class="brand-mark" aria-hidden="true"></div>
      <div class="details">
        <h2 class="business-name">Marcus Ellery Coaching.</h2>
        <p class="person-name">Owen Hartley</p>
        <div class="contact">
          <p class="contact-line contact-line--phone">0213659042</p>
          <p class="contact-line">ohartley@ellerycoach.net</p>
        </div>
      </div>
    </div>
  </section>

</body>
</html>
```